Maple Bus Card

i own a building in the bronx ny - its called "Maple 7 on 2 HDFC"i want a classy logo / business card - nothing too religuous but it is like a family there - its a large apartment building - colors i like dark red, black, medium shade of gray also reg business card stuff tel # 914-555-0173 address 4738 Larkwell Ave Bronx NY 10460 Email fijosh@aol.comslogan - " from many we are one "i can send u a picture of the building for the backside

```html
<!DOCTYPE html>
<html lang="en">
<head>
<meta charset="utf-8">
<title>Maple 7 on 2 HDFC — Business Card</title>
<link rel="stylesheet" href="https://fonts.googleapis.com/css2?family=Source+Sans+3:wght@400;600&family=Roboto+Condensed:wght@400&display=swap">
<style>
  :root {
    --stage: #e9e7e5;
    --card-dark: #2b2a2b;
    --brand-red: #d40b10;
    --mid-gray: #c9c9c9;
    --text-light: #f2f2f2;
  }
  * { box-sizing: border-box; margin: 0; padding: 0; }
  html, body {
    width: 1200px;
    height: 900px;
    overflow: hidden;
    background: var(--stage);
  }
  .card {
    position: absolute;
    left: 150px;
    top: 172px;
    width: 900px;
    height: 555px;
    background: var(--card-dark);
    overflow: hidden;
    font-family: "Source Sans 3", "Helvetica Neue", Arial, sans-serif;
    box-shadow: 0 10px 30px rgba(0,0,0,0.18);
  }
  .card__band {
    position: absolute;
    inset: 0;
    width: 900px;
    height: 555px;
  }
  .brand {
    position: absolute;
    left: 52px;
    top: 58px;
    display: flex;
    align-items: center;
    gap: 26px;
  }
  .brand__mark {
    width: 70px;
    height: 70px;
    background: var(--brand-red);
  }
  .brand__name {
    color: var(--brand-red);
    font-weight: 600;
    font-size: 48px;
    line-height: 50px;
  }
  .slogan {
    position: absolute;
    left: 52px;
    top: 282px;
    font-family: "Roboto Condensed", "Arial Narrow", sans-serif;
    font-size: 26px;
    color: var(--mid-gray);
    text-transform: uppercase;
    letter-spacing: 0.2px;
  }
  .contact {
    position: absolute;
    right: 44px;
    top: 50px;
    text-align: right;
    color: var(--text-light);
    font-size: 25px;
    line-height: 33px;
  }
  .contact__name {
    color: var(--brand-red);
    font-size: 31px;
    font-weight: 600;
    text-transform: uppercase;
    line-height: 36px;
  }
  .contact__role { margin-bottom: 12px; }
  .contact__line {
    display: flex;
    justify-content: flex-end;
    align-items: center;
    gap: 4px;
  }
  .contact__icon { width: 20px; height: 20px; fill: var(--brand-red); }
  .contact__address { margin-top: 18px; }
</style>
</head>
<body>
  <div class="card">
    <svg class="card__band" viewBox="0 0 900 555" aria-hidden="true">
      <path d="M0,320 Q450,710 900,334 L900,555 L0,555 Z" fill="var(--brand-red)"/>
    </svg>

    <div class="brand">
      <div class="brand__mark"></div>
      <div class="brand__name">Maple<br>7 on 2<br>HDFC</div>
    </div>

    <p class="slogan">From many we are one</p>

    <div class="contact">
      <p class="contact__name">Daniel Okafor</p>
      <p class="contact__role">Managing Director</p>
      <p class="contact__line">914-555-0173
        <svg class="contact__icon" viewBox="0 0 20 20" aria-hidden="true"><path d="M4 4c2-2 4-2 5 0l1 2c.5 1 0 2-1 2.5l-1 .5c.8 1.7 2 2.9 3.6 3.6l.5-1c.5-1 1.5-1.5 2.5-1l2 1c2 1 2 3 0 5-3 3-9 0-12-3S1 7 4 4z"/></svg>
      </p>
      <p class="contact__line">mavreld@quintmail.com
        <svg class="contact__icon" viewBox="0 0 20 20" aria-hidden="true"><path d="M2 5h16v10H2z M3 6l7 5 7-5" fill="var(--brand-red)" stroke="var(--card-dark)" stroke-width="1.4"/></svg>
      </p>
      <p class="contact__address">4738 Larkwell Ave<br>Bronx NY 10460</p>
    </div>
  </div>
</body>
</html>
```